Need a vitamin/supplement label

Hi,
I need a vitamin label designing for a product that will be sold online.
The label needs to have the following information on the front:
1) B12
2) Methycobalamin
3) 1000mcg
4) 90 Lozenges
5) Sublingual
6) Dietary Supplement
7) Vegetarian
Numbers 1 and 2 need to standout the most because the product will only be sold online so visibility is key.
Use this design as an inspiration:
http://www.shopvelmara.com/Corvelle-Naturals-Methylcobalamin-5000mcg-Lozenges/dp/Q7742KXRTA/ref=sr_1_2?ie=UTF8&qid=1381433791&sr=8-2&keywords=b12
The label should come across as premium.
The brand name is 'Quarlen Nutra' and I haven't had a logo designed so there's some freedom when it comes to that. It needs to be simple and clean.
If you need any clarifications then let me know.
Online

```html
<!DOCTYPE html>
<html lang="en">
<head>
<meta charset="utf-8">
<title>Quarlen Nutra B12 Label</title>
<link rel="stylesheet" href="https://fonts.googleapis.com/css2?family=Arimo:wght@700&family=Bebas+Neue&family=Raleway:wght@500;600&display=swap">
<style>
  :root {
    --label-blue: #5185bd;
    --tab-blue: #a8c3e2;
    --count-blue: #a9c1de;
    --paper: #ffffff;
    --soft-white: #f1f4f8;
    --brand-ink: #46577f;
    --edge: #c9d3df;
  }
  html, body {
    margin: 0;
    width: 1200px;
    height: 699px;
    overflow: hidden;
    background: var(--paper);
  }
  .label {
    position: absolute;
    left: 347px;
    top: 86px;
    width: 505px;
    height: 527px;
    background: var(--label-blue);
    outline: 1px solid var(--edge);
    overflow: hidden;
    color: var(--paper);
  }
  .label-shapes {
    position: absolute;
    inset: 0;
  }
  .brand {
    position: absolute;
    left: 260px;
    top: 34px;
    width: 230px;
    text-align: center;
    font-family: "Raleway", sans-serif;
    font-weight: 600;
    font-size: 25px;
    letter-spacing: 0.5px;
    color: var(--brand-ink);
    margin: 0;
  }
  .product-name {
    position: absolute;
    left: 40px;
    top: 78px;
    margin: 0;
    font-family: "Bebas Neue", sans-serif;
    font-weight: 400;
    font-size: 166px;
    line-height: 1;
    letter-spacing: 4px;
  }
  .compound {
    position: absolute;
    left: 42px;
    top: 224px;
    margin: 0;
    font-family: "Arimo", sans-serif;
    font-weight: 700;
    font-size: 36px;
    line-height: 1;
  }
  .strength {
    position: absolute;
    left: 43px;
    top: 264px;
    margin: 0;
    font-family: "Arimo", sans-serif;
    font-weight: 400;
    font-size: 22px;
  }
  .category {
    position: absolute;
    left: 43px;
    top: 382px;
    margin: 0;
    font-family: "Bebas Neue", sans-serif;
    font-size: 44px;
    line-height: 1;
    letter-spacing: 0.3px;
  }
  .count-box {
    position: absolute;
    left: 44px;
    top: 432px;
    width: 61px;
    height: 95px;
    background: var(--count-blue);
    text-align: center;
    font-family: "Bebas Neue", sans-serif;
  }
  .count-number {
    display: block;
    font-size: 56px;
    line-height: 1;
    margin-top: 12px;
  }
  .count-unit {
    display: block;
    font-size: 11px;
    letter-spacing: 0.4px;
  }
  .attributes {
    position: absolute;
    left: 114px;
    top: 432px;
    margin: 0;
    padding: 0;
    list-style: none;
    font-family: "Raleway", sans-serif;
    font-weight: 500;
    font-size: 26px;
    line-height: 33px;
    letter-spacing: 0.6px;
  }
</style>
</head>
<body>
  <section class="label">
    <svg class="label-shapes" width="505" height="527" viewBox="0 0 505 527" aria-hidden="true">
      <path d="M232 48 L232 30 Q232 19 246 19 L505 19 L505 48 Z" fill="var(--tab-blue)"/>
      <rect x="0" y="48" width="505" height="34" fill="var(--paper)"/>
      <rect x="23" y="82" width="6" height="445" fill="var(--paper)"/>
      <path d="M228 527 C300 420 400 352 505 326 L505 527 Z" fill="var(--tab-blue)"/>
      <path d="M250 527 C322 432 410 372 505 344 L505 527 Z" fill="var(--soft-white)"/>
    </svg>

    <p class="brand">Quarlen Nutra</p>

    <h1 class="product-name">B12</h1>
    <h2 class="compound">Methycobalamin</h2>
    <p class="strength">1000mcg</p>

    <p class="category">Dietary Supplement</p>
    <div class="count-box">
      <span class="count-number">90</span>
      <span class="count-unit">LOZENGES</span>
    </div>
    <ul class="attributes">
      <li>Sublingual</li>
      <li>Vegetarian</li>
    </ul>
  </section>
</body>
</html>
```